New Webpage for High Class Expert Witness Services Company

We are looking for a minimalist design for a webpage that just has our logo and an entry form offer to connect with one of our Liaisons.
The entry form should just ask for Name, Email, Contact Info and Description of Project.

Company Name is: The Marlowe Crest Advisory Services

Number of Pages Required

1 page

```html
<!DOCTYPE html>
<html lang="en">
<head>
<meta charset="UTF-8">
<title>The Marlowe Crest Advisory Services — Request Consultation</title>
<link href="https://fonts.googleapis.com/css2?family=Cinzel:wght@400;600&family=Montserrat:wght@300;400;600&display=swap" rel="stylesheet">
<style>
  :root {
    --page-bg: #111111;
    --facet-bg: #161616;
    --card-bg: #1f1f1f;
    --card-edge: #2e2e2e;
    --text-main: #ece9e3;
    --text-soft: #9a9894;
    --field-bg: #e6e6e6;
    --gold: #7d5f28;
    --gold-text: #e9dcc0;
  }
  * { box-sizing: border-box; margin: 0; padding: 0; }
  html, body { width: 1200px; height: 840px; overflow: hidden; }
  body {
    position: relative;
    background: var(--page-bg);
    font-family: 'Montserrat', sans-serif;
    color: var(--text-main);
  }
  .backdrop { position: absolute; inset: 0; width: 1200px; height: 840px; }
  .page { position: relative; z-index: 1; display: flex; flex-direction: column; align-items: center; }

  .brand {
    margin-top: 48px;
    display: flex; align-items: center; gap: 12px;
  }
  .brand-mark { width: 30px; height: 30px; background: var(--text-main); }
  .brand-name {
    font-family: 'Cinzel', serif; font-weight: 400;
    font-size: 20px; letter-spacing: 0.06em; color: var(--text-main);
  }

  .headline {
    margin-top: 52px;
    font-family: 'Cinzel', serif; font-weight: 400;
    font-size: 32px; line-height: 1.2; text-align: center; letter-spacing: 0.03em;
  }
  .headline strong { font-weight: 600; }
  .subline {
    margin-top: 14px;
    font-size: 15px; font-weight: 300; color: var(--text-soft); letter-spacing: 0.02em;
  }

  .inquiry-card {
    margin-top: 30px;
    width: 360px;
    background: var(--card-bg);
    border: 1px solid var(--card-edge);
    border-radius: 18px;
    padding: 22px 64px 24px;
  }
  .inquiry-title {
    margin: 0 -40px;
    text-align: center; white-space: nowrap;
    font-size: 19px; line-height: 22px; font-weight: 300; color: #cfccc6;
  }
  .inquiry-title strong { font-weight: 600; color: var(--text-main); }
  .field { margin-top: 12px; }
  .field:first-of-type { margin-top: 24px; }
  .field label { display: block; font-size: 10px; line-height: 12px; color: var(--text-main); margin-bottom: 3px; }
  .field input, .field textarea {
    display: block; width: 100%; height: 34px;
    background: var(--field-bg); border: none; border-radius: 2px;
    font-family: inherit;
  }
  .field textarea { height: 88px; resize: none; }
  .submit {
    display: block; width: 100%; height: 32px; margin-top: 14px;
    background: var(--gold); color: var(--gold-text);
    border: none; font-family: inherit; font-size: 11px; letter-spacing: 0.02em;
  }
</style>
</head>
<body>
  <svg class="backdrop" viewBox="0 0 1200 840" aria-hidden="true">
    <polygon points="600,0 1200,0 1200,210" fill="var(--facet-bg)"/>
    <polygon points="0,420 330,260 240,790 0,790" fill="#0f0f0f"/>
    <polygon points="240,790 330,260 860,260 860,790" fill="#141414"/>
  </svg>

  <main class="page">
    <header class="brand">
      <span class="brand-mark"></span>
      <span class="brand-name">The Marlowe Crest Advisory Services</span>
    </header>

    <h1 class="headline">When the stakes are <strong>absolute,</strong><br>the standard must be too.</h1>
    <p class="subline">Expert witness integration &amp; legal defense support</p>

    <form class="inquiry-card">
      <h2 class="inquiry-title">Tell us about Your <strong>Matter</strong></h2>
      <div class="field"><label for="full-name">Full Name</label><input id="full-name" type="text"></div>
      <div class="field"><label for="email">Email</label><input id="email" type="email"></div>
      <div class="field"><label for="phone">Contact Number</label><input id="phone" type="tel"></div>
      <div class="field"><label for="project">Description of Project</label><textarea id="project"></textarea></div>
      <button class="submit" type="button">Request Consultation</button>
    </form>
  </main>
</body>
</html>
```